single page with calendar booking ability

a single web page that has the ability to book calendar times and dates, also needs to be able to link to my other business social media seamlessly. I don't want to get multiple developers and or agency's involved, I want you the web designer to design it and make sure it's up and works as described
. The boats we work on are between 20 feet to 40 feet, bow riders , cabin cruisers, and center consoles. The brands that we work on include but are not limited to Velmora, Praxen, Dunby Vale, Lark mil, Quilvane, Brevik, Drelo, and many more. Winterization and shrink wrapping is completely different than graphic wrapping, we do not do graphic's wrapping. Also, only 5% of our business will be auto detailing, the rest will be boats on trailers. Please ensure that the calendar booking system is intergraded and not a surprise to me later

Target Market(s)

Lakes region New Hampshire

Industry/Entity Type

marine

Coding

Coded - Design and coding required

Number of Pages Required

1 page

Colors
0054AA
0677BA
7BADD7
CADEEF
E8F1F8
00AB8E
00BBA5
67D7C9
C6EFE9
E9F9F6
EE7325
F08F49
F5BC92
FAE3D3
FDF4ED

Requirements
Must have
• calendar booking capability
Nice to have
• Pictures of boats being shrink wrapped for the winter season, Nice before and after pictures of boats detailed, only 5% of our business is auto detailing
Should not have
• Large yachts, lots of sail boats as we only do a few, graphics wrapping.. we don't graphic wrap

```html
<!DOCTYPE html>
<html lang="en">
<head>
<meta charset="utf-8">
<title>Harbor Keel – Boat Care, Lakes Region NH</title>
<link href="https://fonts.googleapis.com/css2?family=Montserrat:wght@600;700&family=Roboto:wght@400;500;700&display=swap" rel="stylesheet">
<style>
:root{
  --orange:#EE7325;
  --orange-soft:#F08F49;
  --teal:#00AB8E;
  --teal-bright:#00BBA5;
  --teal-pale:#EDF8F6;
  --blue-deep:#0054AA;
  --blue:#0677BA;
  --ink:#222222;
  --text:#555555;
  --footer:#252525;
  --white:#ffffff;
}
*{box-sizing:border-box;margin:0;padding:0}
html,body{width:1200px;height:3977px;overflow:hidden}
body{font-family:'Roboto',Arial,sans-serif;color:var(--ink);background:var(--white);position:relative}
.abs{position:absolute}
h1,h2,h3{font-family:'Montserrat',Arial,sans-serif;font-weight:700}

/* header */
.site-header{position:absolute;left:0;top:0;width:1200px;height:93px;background:var(--white)}
.brand{position:absolute;left:111px;top:30px;display:flex;align-items:center;gap:10px;font-family:'Roboto',sans-serif;font-weight:700;font-size:24px;color:var(--blue-deep)}
.brand-mark{width:22px;height:22px;border-radius:50%;background:var(--orange)}
.main-nav{position:absolute;left:301px;top:38px;display:flex;gap:22px;font-size:13.5px;font-weight:500;text-transform:uppercase}
.call-box{position:absolute;left:746px;top:0;width:454px;height:93px;background:var(--orange);clip-path:polygon(48px 0,100% 0,100% 100%,0 100%)}
.call-icon{position:absolute;left:128px;top:21px;width:50px;height:50px;border-radius:50%;background:var(--white);display:flex;align-items:center;justify-content:center}
.call-label{position:absolute;left:205px;top:24px;color:var(--white);font-size:14px;font-weight:500}
.call-number{position:absolute;left:205px;top:46px;color:var(--white);font-size:22px;font-weight:500}

/* hero */
.hero{position:absolute;left:0;top:93px;width:1200px;height:600px;background:linear-gradient(160deg,#3a6ea8 0%,#1f5594 45%,#2a5c99 100%)}
.hero-photo{position:absolute;inset:0;background:radial-gradient(ellipse 380px 260px at 880px 300px,rgba(235,242,250,.55),transparent 70%)}
.hero h1{position:absolute;left:111px;top:204px;color:var(--white);font-size:31px;font-weight:700;letter-spacing:.3px}
.hero p{position:absolute;left:111px;top:257px;width:560px;color:var(--white);font-size:17px;font-weight:500;line-height:27px}
.btn{display:inline-block;background:var(--orange);color:var(--white);font-weight:700;font-size:14px;text-transform:uppercase;text-align:center}
.hero .btn{position:absolute;left:111px;top:339px;width:127px;height:51px;line-height:51px}

/* section heads */
.section-title{position:absolute;left:0;width:1200px;text-align:center;font-size:37px;color:var(--ink)}
.rule{position:absolute;height:3px;width:110px;background:var(--teal)}

/* mission */
.mission-intro{position:absolute;left:260px;top:848px;width:680px;text-align:center;font-size:14.5px;line-height:24px;color:var(--text)}
.card{position:absolute;top:937px;width:311px;height:298px;background:var(--white);box-shadow:0 0 8px rgba(0,0,0,.14);padding:30px 13px 0}
.card.is-active{background:var(--orange);color:var(--white)}
.card h3{font-family:'Roboto',sans-serif;font-size:18px;font-weight:700;line-height:27px;margin-top:22px;text-transform:uppercase}
.card p{font-size:13px;line-height:22px;margin-top:18px;text-align:justify}
.card.is-active p{color:var(--white)}

/* what we do */
.what-we-do{position:absolute;left:0;top:1328px;width:1200px;height:514px;background:var(--teal-pale)}
.photo{position:absolute}
.side-title{position:absolute;left:653px;font-size:32px;color:var(--ink)}
.side-text{position:absolute;left:653px;width:436px;font-size:13.5px;line-height:24px;color:var(--text);text-align:justify}

/* stats */
.stats{position:absolute;left:0;top:1842px;width:1200px;height:326px;background:linear-gradient(90deg,#0d8f7c,#129f88 50%,#0a8d79)}
.stat{position:absolute;top:0;width:340px;text-align:center;color:var(--white)}
.stat svg{margin-top:45px}
.stat-value{font-family:'Roboto',sans-serif;font-weight:700;font-size:43px;margin-top:22px}
.stat-label{font-size:16px;font-weight:500;line-height:24px;margin-top:12px}

/* news */
.news-card{position:absolute;top:2829px;width:313px;height:368px}
.news-photo{height:219px}
.news-body{position:absolute;left:12px;top:196px;width:289px;height:172px;background:var(--white);box-shadow:0 0 8px rgba(0,0,0,.12);padding:18px 14px}
.news-date{font-size:14px;color:var(--text);display:flex;align-items:center;gap:10px}
.news-body h3{font-family:'Roboto',sans-serif;color:var(--orange);font-size:21px;font-weight:700;margin-top:9px}
.news-body p{font-size:13px;line-height:22px;color:var(--text);margin-top:10px}
.slider-arrow{position:absolute;top:2925px}

/* bookings */
.footer{position:absolute;left:0;top:3570px;width:1200px;height:350px;background:var(--footer)}
.bookings{position:absolute;left:111px;top:3292px;width:978px;height:385px;background:linear-gradient(120deg,#ef7a2f,#ec7024 60%,#ef7b31)}
.bookings h2{position:absolute;left:37px;top:64px;color:var(--white);font-size:33px}
.bookings .rule{left:37px;top:112px;width:148px;background:var(--white)}
.bookings p{position:absolute;left:37px;top:142px;width:456px;color:var(--white);font-size:13.5px;line-height:24px}
.bookings .date{top:225px;font-weight:500}
.bookings .btn{position:absolute;left:40px;top:271px;width:125px;height:51px;line-height:51px;background:var(--white);color:var(--orange)}
.calendar{position:absolute;left:553px;top:37px;width:386px;height:316px;background:var(--white)}
.cal-head{position:absolute;left:0;top:18px;width:386px;text-align:center;font-size:15px;font-weight:500}
.cal-grid{position:absolute;left:8px;top:60px;display:grid;grid-template-columns:repeat(7,52.8px);grid-auto-rows:42.5px}
.cal-grid span{display:flex;align-items:center;justify-content:center;font-size:15px;color:var(--ink)}
.cal-grid .dow{font-weight:500;height:42.5px}
.cal-grid .muted{color:#aaa}
.cal-grid .open{outline:2px solid var(--teal);outline-offset:-4px;color:var(--teal)}
.cal-grid .picked{background:var(--teal);color:var(--white)}

/* footer */
.f-brand{position:absolute;left:111px;top:3738px;display:flex;align-items:center;gap:10px;font-size:24px;font-weight:700;color:var(--white)}
.socials{position:absolute;left:125px;top:3832px;display:flex;gap:10px}
.socials span{width:34px;height:34px;border:1.5px solid var(--white);border-radius:50%;display:flex;align-items:center;justify-content:center}
.socials i{width:10px;height:10px;background:var(--white);border-radius:2px}
.f-col{position:absolute;top:3730px;color:var(--white)}
.f-col h4{font-size:17px;font-weight:700;margin-bottom:26px}
.f-links li{list-style:none;font-size:15px;line-height:26px;display:flex;align-items:center;gap:18px}
.f-links li::before{content:"";width:9px;height:9px;border:2px solid var(--orange);border-radius:50%}
.f-col p{font-size:13px;line-height:21px}
.subscribe{margin-top:24px;width:256px;height:38px;background:var(--white);display:flex;align-items:center;justify-content:space-between;padding-left:12px;font-size:12.5px;color:#888}
.subscribe b{width:32px;height:32px;margin-right:4px;background:var(--orange);display:flex;align-items:center;justify-content:center}
.contact-row{display:flex;gap:22px;font-size:15px;line-height:26px;margin-bottom:8px}
.bottom-bar{position:absolute;left:0;top:3920px;width:1200px;height:57px;background:var(--teal);color:var(--white);font-size:13px;text-align:center;line-height:57px}
</style>
</head>
<body>

<header class="site-header">
  <div class="brand"><span class="brand-mark"></span>Harbor Keel</div>
  <nav class="main-nav"><span>Home</span><span>Our Mission</span><span>Analysis</span><span>Marketing</span><span>Blog</span></nav>
  <div class="call-box">
    <div class="call-icon"><svg width="24" height="24" viewBox="0 0 24 24"><path d="M6 3l4 4-2 3c1 2 3 4 6 6l3-2 4 4-3 3C10 21 3 14 3 6z" fill="var(--orange)"/></svg></div>
    <div class="call-label">Call Us:</div>
    <div class="call-number">555-014-2290</div>
  </div>
</header>

<section class="hero">
  <div class="hero-photo" role="img" aria-label="Motor boat cutting a white wake across deep blue lake water"></div>
  <h1>WELCOME TO HARBOR KEEL</h1>
  <p>We are on a mission to support boat and car owners to keep their vessels and cars clean, well maintained</p>
  <span class="btn">Book Now</span>
</section>

<h2 class="section-title" style="top:778px">OUR MISSION</h2>
<div class="rule" style="left:545px;top:826px"></div>
<p class="mission-intro">We aim to run a company focused on providing customers in the lakes region of the central New Hampshire with a broad range of premium boats and cars services.</p>

<article class="card" style="left:111px">
  <svg width="70" height="66" viewBox="0 0 70 66" fill="none" stroke="var(--orange)" stroke-width="2"><circle cx="40" cy="26" r="22"/><path d="M24 42L6 60"/><path d="M30 34v-8M38 34v-14M46 34v-10"/><circle cx="54" cy="54" r="9"/></svg>
  <h3>Huge<br>Market Potential</h3>
  <p>Lorem ipsum dolor sit amet, consectetur adip iscing elit, sed do eiusmod tempor in cidi dunt ut labore et dolopiscing elit, sed do eiusmore magna aliqua.</p>
</article>
<article class="card is-active" style="left:445px">
  <svg width="70" height="66" viewBox="0 0 70 66" fill="none" stroke="var(--white)" stroke-width="2"><circle cx="35" cy="14" r="11"/><path d="M4 40l14-10 14 8 14-8 14 10-18 14-10-6-10 6z"/></svg>
  <h3>Solid<br>Business Concept</h3>
  <p>Lorem ipsum dolor sit amet, consectetur adip iscing elit, sed do eiusmod tempor in cidi dunt ut labore et dolopiscing elit, sed do eiusmore magna aliqua.</p>
</article>
<article class="card" style="left:777px">
  <svg width="70" height="66" viewBox="0 0 70 66" fill="none" stroke="var(--orange)" stroke-width="2"><circle cx="32" cy="34" r="26"/><circle cx="32" cy="34" r="16"/><circle cx="32" cy="34" r="7"/><path d="M32 2v10M32 56v10M0 34h10M54 34h10"/></svg>
  <h3>Attractive<br>Investment Prospect</h3>
  <p>Lorem ipsum dolor sit amet, consectetur adip iscing elit, sed do eiusmod tempor in cidi dunt ut labore et dolopiscing elit, sed do eiusmore magna aliqua.</p>
</article>

<section class="what-we-do">
  <div class="photo" style="left:111px;top:66px;width:488px;height:384px;background:linear-gradient(135deg,#e4a38f 0%,#7aa5c9 40%,#1f6fb4 100%)" role="img" aria-label="Motor boat speeding across the lake at sunset"></div>
  <h2 class="side-title" style="top:82px">WHAT WE DO</h2>
  <div class="rule" style="left:653px;top:128px"></div>
  <p class="side-text" style="top:164px">We aim to run a company focused on providing customers in the lakes region of the central New Hampshire with a broad range of boats and cars services, including but not limited to shrink wrap for boats, mobile detailing for boats and cars, mobile winterization for boats and much more.</p>
  <p class="side-text" style="top:306px">We already own a company operating a floating bar and restaurant on Lake Winnipesaukee with a strong social media following and want to leverage on our existing audience to obtain hundreds of thousands of views and interactions every day to nurture positive word of mouth and organic advertising.</p>
</section>

<section class="stats" role="img" aria-label="Boat moored by a rocky coast, in teal tones">
  <div class="stat" style="left:93px">
    <svg width="90" height="90" viewBox="0 0 90 90" fill="none" stroke="var(--white)" stroke-width="3"><path d="M35 30h20v38H35zM38 18h14v12H38zM45 10v8M20 30a28 28 0 000 28M70 30a28 28 0 010 28M10 74q8-6 16 0t16 0 16 0 16 0 16 0M10 84q8-6 16 0t16 0 16 0 16 0 16 0"/></svg>
    <div class="stat-value">$73.91 B</div>
    <div class="stat-label">marine services market size in 2021</div>
  </div>
  <div class="stat" style="left:430px">
    <svg width="90" height="90" viewBox="0 0 90 90" fill="none" stroke="var(--white)" stroke-width="3"><path d="M12 78V56M24 78V46M36 78V52M48 78V40M12 44l18-14 12 8 24-22M56 16h10v10"/><circle cx="62" cy="62" r="12"/><path d="M71 71l10 10"/></svg>
    <div class="stat-value">+4.70%</div>
    <div class="stat-label">compounded annual growth until 2028</div>
  </div>
  <div class="stat" style="left:767px">
    <svg width="90" height="90" viewBox="0 0 90 90" fill="none" stroke="var(--white)" stroke-width="4"><path d="M20 74L70 24M62 12a14 14 0 0016 16l-8 8-16-16zM20 16l12 12M14 22l12 12M56 56l18 18-6 6-18-18"/></svg>
    <div class="stat-value">$101.98 B</div>
    <div class="stat-label">forecasted marine services market size<br>within the next seven years</div>
  </div>
</section>

<div class="photo" style="left:111px;top:2262px;width:488px;height:387px;background:var(--white);box-shadow:0 0 6px rgba(0,0,0,.15)">
  <div style="position:absolute;left:7px;top:7px;right:7px;bottom:7px;background:linear-gradient(150deg,#1c5a91,#0d4678 50%,#1b5d99)" role="img" aria-label="Aerial view of a cabin cruiser on open water"></div>
</div>
<h2 class="side-title" style="top:2283px">MARKETING STRATEGY</h2>
<div class="rule" style="left:653px;top:2329px"></div>
<p class="side-text" style="top:2364px">Our business model is centered on the offering of a broad range of solutions to coat, protect, clean, winterize and maintain vessels and cars in central New Hampshire through a seamless and smooth digital booking process. Our potential customers will be able to discover more about our services selection through online discovery touchpoints including social media, our website, and online services aggregators.</p>
<span class="btn abs" style="left:653px;top:2568px;width:125px;height:51px;line-height:51px">Read More</span>

<h2 class="section-title" style="top:2733px">LATEST NEWS</h2>
<div class="rule" style="left:545px;top:2779px"></div>
<svg class="slider-arrow" style="left:52px" width="20" height="30" viewBox="0 0 20 30"><path d="M16 2L4 15l12 13" fill="none" stroke="var(--orange)" stroke-width="3"/></svg>
<svg class="slider-arrow" style="left:1128px" width="20" height="30" viewBox="0 0 20 30"><path d="M4 2l12 13L4 28" fill="none" stroke="var(--orange)" stroke-width="3"/></svg>

<article class="news-card" style="left:111px">
  <div class="news-photo" style="background:linear-gradient(135deg,#2b2f36,#8a8f96 60%,#d6d9dc)" role="img" aria-label="Technician servicing an outboard motor"></div>
  <div class="news-body"><div class="news-date"><svg width="14" height="14" viewBox="0 0 14 14"><rect x="1" y="2" width="12" height="11" fill="none" stroke="var(--teal)" stroke-width="1.5"/><path d="M1 5h12" stroke="var(--teal)" stroke-width="1.5"/></svg>11 Sep 2021</div><h3>Sed ut perspiciatis Lorm</h3><p>Lorem ipsum dolor sit amet, consectet ur adipiscing elit, sed do eiusmod temp or incididunt ut laborea.</p></div>
</article>
<article class="news-card" style="left:444px">
  <div class="news-photo" style="background:linear-gradient(180deg,#9fc2e0,#e9eef2 55%,#7a6a5e)" role="img" aria-label="Motor boat on stands in a boatyard"></div>
  <div class="news-body"><div class="news-date"><svg width="14" height="14" viewBox="0 0 14 14"><rect x="1" y="2" width="12" height="11" fill="none" stroke="var(--teal)" stroke-width="1.5"/><path d="M1 5h12" stroke="var(--teal)" stroke-width="1.5"/></svg>11 Sep 2021</div><h3>Sed ut perspiciatis Lorm</h3><p>Lorem ipsum dolor sit amet, consectet ur adipiscing elit, sed do eiusmod temp or incididunt ut laborea.</p></div>
</article>
<article class="news-card" style="left:776px">
  <div class="news-photo" style="background:linear-gradient(135deg,#d98a4b,#5a6f8a 55%,#c9ccd0)" role="img" aria-label="Hands polishing a boat propeller"></div>
  <div class="news-body"><div class="news-date"><svg width="14" height="14" viewBox="0 0 14 14"><rect x="1" y="2" width="12" height="11" fill="none" stroke="var(--teal)" stroke-width="1.5"/><path d="M1 5h12" stroke="var(--teal)" stroke-width="1.5"/></svg>11 Sep 2021</div><h3>Sed ut perspiciatis Lorm</h3><p>Lorem ipsum dolor sit amet, consectet ur adipiscing elit, sed do eiusmod temp or incididunt ut laborea.</p></div>
</article>

<footer class="footer"></footer>

<section class="bookings">
  <h2>OUR BOOKINGS</h2>
  <div class="rule"></div>
  <p>Lorem ipsum dolor sit amet, consectetur adipiscing elit, sed do eiusm od tempor incididunt ut labore et dolore magna aliqua. Ut enim ad minim veniam, quis nostrud exercitationa.</p>
  <p class="date">Book Date: 11 Sep 2021</p>
  <span class="btn">Book Now</span>
  <div class="calendar">
    <div class="cal-head"><span style="color:var(--orange);margin-right:60px">‹</span>September, 2021<span style="color:var(--orange);margin-left:60px">›</span></div>
    <div class="cal-grid">
      <span class="dow">Sun</span><span class="dow">Mon</span><span class="dow">Tue</span><span class="dow">Wed</span><span class="dow">Thu</span><span class="dow">Fri</span><span class="dow">Sat</span>
      <span class="muted">29</span><span class="muted">30</span><span class="muted">31</span><span>1</span><span>2</span><span>3</span><span>4</span>
      <span>5</span><span>6</span><span>7</span><span>8</span><span>9</span><span>10</span><span class="picked">11</span>
      <span class="open">12</span><span>13</span><span>14</span><span>15</span><span class="open">16</span><span>17</span><span>18</span>
      <span>19</span><span>20</span><span class="open">21</span><span>22</span><span>23</span><span>24</span><span>25</span>
      <span>26</span><span>27</span><span>28</span><span>29</span><span class="open">30</span><span class="muted">1</span><span class="muted">2</span>
    </div>
  </div>
</section>

<div class="f-brand"><span class="brand-mark"></span>Harbor Keel</div>
<div class="socials"><span><i></i></span><span><i></i></span><span><i></i></span></div>

<div class="f-col" style="left:337px">
  <h4>Menu Links</h4>
  <ul class="f-links"><li>Home</li><li>Our Mission</li><li>Analysis</li><li>Marketing</li><li>Blog</li></ul>
</div>
<div class="f-col" style="left:525px">
  <h4>Sign Up</h4>
  <p>Join our mailing list to receive the latest<br>news and updates from our team</p>
  <div class="subscribe">Email Address<b><svg width="14" height="14" viewBox="0 0 14 14"><path d="M1 7l12-6-4 12-2-5z" fill="none" stroke="var(--white)" stroke-width="1.5"/></svg></b></div>
</div>
<div class="f-col" style="left:897px">
  <h4>Contact Us</h4>
  <div class="contact-row"><svg width="10" height="14" viewBox="0 0 10 14" style="margin-top:6px"><path d="M5 14S0 7 0 5a5 5 0 0110 0c0 2-5 9-5 9z" fill="var(--orange)"/></svg><span>18 Cove Landing Rd,<br>United States</span></div>
  <div class="contact-row"><svg width="12" height="12" viewBox="0 0 24 24" style="margin-top:7px"><path d="M6 3l4 4-2 3c1 2 3 4 6 6l3-2 4 4-3 3C10 21 3 14 3 6z" fill="var(--orange)"/></svg><span>555-014-2290</span></div>
  <div class="contact-row"><svg width="12" height="12" viewBox="0 0 12 12" style="margin-top:7px"><rect x="1" y="3" width="10" height="8" fill="var(--orange)"/><rect x="3" y="1" width="6" height="3" fill="var(--orange)"/></svg><span>555-014-2290</span></div>
</div>

<div class="bottom-bar">© 2021 Company Name &nbsp;&nbsp;|&nbsp;&nbsp; Privacy policy &nbsp;&nbsp;|&nbsp;&nbsp; Terms Of Use</div>

</body>
</html>
```